project - Misto Den

Dear designers, I'm Looking for an appealing new business card design to represent us for our new e-cigarette store: The Misto Den. Knowledgeable and friendly staff we aim for superior customer service with a positive atmosphere. Classic feel with modern touch is what we are aiming for . Lime green font and grey back round is the original color scheme but we are flexible and open to suggestions. I added some doodles to show you where my mind is at. address: 4827 203 St SW Edmonton, AB (inside the grand swap bazaar)web: themistoden.com email: info@themistoden.com phone : 555.214.6093 Thanks and am looking forward to seeing your creative , fresh and innovative designs.
Good luck everybody!
Gordon
Updates
lime green and charcoal grey please. thanks
Industry/Entity Type
Business
Logo Text
The Misto Den
Look and feel
Each slider illustrates characteristics of the customer's brand and the style your logo design should communicate.

```html
<!DOCTYPE html>
<html lang="en">
<head>
<meta charset="utf-8">
<title>The Misto Den — Business Card</title>
<link rel="stylesheet" href="https://fonts.googleapis.com/css2?family=Quicksand:wght@500;600&family=Playfair+Display:ital@1&display=swap">
<style>
  :root {
    --bg: #0f1a20;
    --charcoal: #1b2127;
    --charcoal-edge: #2a3138;
    --lime: #c4f01c;
    --ink: #131a1f;
    --smoke: #7c858b;
  }
  * { margin: 0; padding: 0; box-sizing: border-box; }
  html, body { width: 1200px; height: 1000px; overflow: hidden; }
  body {
    background: radial-gradient(ellipse at 40% 35%, #1a2a33 0%, var(--bg) 70%);
    font-family: "Quicksand", sans-serif;
    position: relative;
  }
  .card {
    position: absolute;
    width: 525px;
    height: 300px;
    background: var(--charcoal);
    border: 1px solid var(--charcoal-edge);
    box-shadow: 0 18px 40px rgba(0,0,0,.55);
    overflow: hidden;
  }
  .card--back { left: 50px; top: 90px; }
  .card--front { left: 625px; top: 90px; }

  .back__name {
    position: absolute; left: 0; right: 0; top: 112px;
    text-align: center;
    font-size: 15px; font-weight: 500; color: var(--lime);
  }
  .back__band {
    position: absolute; left: 0; right: 0; bottom: 0;
    height: 74px;
    background: var(--lime);
    padding: 12px 18px 0;
    color: var(--ink);
    font-weight: 600;
    font-size: 13px;
    line-height: 1.5;
  }
  .back__rule {
    position: absolute; left: 0; right: 0; bottom: 8px;
    height: 2px; background: var(--ink);
  }

  .front__line {
    position: absolute; left: 70px; top: 0;
    width: 1px; height: 150px; background: var(--lime);
  }
  .front__frame {
    position: absolute; left: 70px; top: 150px;
    width: 360px; height: 100px;
    border-top: 1px solid var(--lime);
    border-right: 1px solid var(--lime);
    border-bottom: 1px solid var(--lime);
  }
  .front__name {
    position: absolute; left: 90px; top: 160px;
    font-size: 40px; font-weight: 500; color: var(--lime);
    white-space: nowrap;
  }
  .front__tag {
    position: absolute; left: 190px; top: 212px;
    font-family: "Playfair Display", serif; font-style: italic;
    font-size: 20px; color: var(--smoke);
  }

  .lockup__line { position: absolute; background: var(--lime); }
  .lockup__top { left: 340px; top: 692px; width: 820px; height: 2px; }
  .lockup__left-drop { left: 338px; top: 692px; width: 2px; height: 138px; }
  .lockup__lead { left: 0; top: 828px; width: 340px; height: 2px; }
  .lockup__right-drop { left: 1158px; top: 692px; width: 2px; height: 220px; }
  .lockup__tail { left: 1158px; top: 910px; width: 42px; height: 2px; }
  .lockup__name {
    position: absolute; left: 362px; top: 700px;
    font-size: 104px; font-weight: 500; color: var(--lime);
    letter-spacing: -1px; white-space: nowrap; line-height: 1.2;
  }
  .lockup__tag {
    position: absolute; left: 660px; top: 850px;
    font-family: "Playfair Display", serif; font-style: italic;
    font-size: 50px; color: var(--smoke);
  }
</style>
</head>
<body>
  <section class="card card--back" aria-label="Card back with contact details">
    <p class="back__name">The Misto Den</p>
    <div class="back__band">
      <p>4827 203 St SW Edmonton, AB (inside the grand swap bazaar)</p>
      <p>web: themistoden.com | email: info@themistoden.com | phone : 555.214.6093</p>
    </div>
    <span class="back__rule"></span>
  </section>

  <section class="card card--front" aria-label="Card front with store name">
    <span class="front__line"></span>
    <span class="front__frame"></span>
    <p class="front__name">The Misto Den</p>
    <p class="front__tag">e-cigarette store</p>
  </section>

  <section class="lockup" aria-label="Store name lockup">
    <span class="lockup__line lockup__top"></span>
    <span class="lockup__line lockup__left-drop"></span>
    <span class="lockup__line lockup__lead"></span>
    <span class="lockup__line lockup__right-drop"></span>
    <span class="lockup__line lockup__tail"></span>
    <p class="lockup__name">The Misto Den</p>
    <p class="lockup__tag">e-cigarette store</p>
  </section>
</body>
</html>
```